Velvet Lantern rebranding my business with a new business card

I have my new logo and now I need a refresher on my business cards. I really want something fun and fresh. I like black background or anything to make the color pop.
Logo
Name: Velvet Lantern
Contact Info as stated below:
Mira Pellow
555-013-4762
Logo
Name: Velvet Lantern
Mira Pellow
555-013-4762
fb.me/VelvetLanternbyMira
Instagram: @VelvetLanternbyMira

Industry/Entity Type

Business

Contact Information for Business Card

double-sided. Logo on one side. Contact info on the other.

Requirements
Must have
• Logo
• Name: Velvet Lantern
• Contact Info as stated below:
• Mira Pellow
• 555-013-4762
• fb.me/VelvetLanternbyMira
• fb.me/VelvetLanternbyMira

```html
<!DOCTYPE html>
<html lang="en">
<head>
<meta charset="utf-8">
<title>Velvet Lantern — Business Card</title>
<link rel="stylesheet" href="https://fonts.googleapis.com/css2?family=Roboto+Slab:wght@700&family=Roboto:wght@400&display=swap">
<style>
  :root {
    --backdrop: #e9e6e1;
    --card-white: #ffffff;
    --card-black: #050505;
    --ink: #1a1a1a;
    --ink-soft: #555555;
    --pink: #f4b6c6;
    --pink-ring: #f2c6d2;
    --teal: #6ccfc0;
    --beige: #d6cdb3;
    --on-dark: #e8e8e8;
  }
  * { box-sizing: border-box; margin: 0; padding: 0; }
  html, body { width: 1200px; height: 911px; overflow: hidden; }
  body {
    background: var(--backdrop);
    font-family: "Roboto", Arial, sans-serif;
    position: relative;
  }
  .card {
    position: absolute;
    width: 540px;
    height: 310px;
    border-radius: 18px;
    overflow: hidden;
    box-shadow: 0 10px 28px rgba(0,0,0,0.18);
  }
  /* Contact side */
  .card-front { left: 40px; top: 300px; background: var(--card-white); }
  .edge-band {
    position: absolute; right: 0; top: 0; bottom: 0; width: 16px;
    display: flex; flex-direction: column;
  }
  .edge-band span { flex: 1; }
  .band-black { background: var(--card-black); }
  .band-beige { background: var(--beige); }
  .band-teal { background: var(--teal); }
  .band-pink { background: var(--pink); }
  .logo-badge {
    position: absolute;
    border-radius: 50%;
    background: var(--card-white);
    border: 3px solid var(--pink-ring);
    box-shadow: 0 0 0 2px var(--card-white), 0 0 0 3px #cfcfcf;
    display: flex; align-items: center; justify-content: center;
    text-align: center;
    font-family: "Roboto Slab", Georgia, serif;
    font-weight: 700;
    color: var(--ink);
    line-height: 1.1;
  }
  .card-front .logo-badge { width: 124px; height: 124px; left: 340px; top: 34px; font-size: 16px; }
  .holder-name {
    position: absolute; left: 40px; top: 196px;
    font-family: "Roboto Slab", Georgia, serif; font-weight: 700;
    font-size: 22px; letter-spacing: 0.5px; color: var(--ink);
  }
  .contact-list {
    position: absolute; left: 40px; top: 230px;
    list-style: none; font-size: 13px; color: var(--ink-soft);
  }
  .contact-list li { display: flex; align-items: center; gap: 8px; height: 19px; }
  .contact-list svg { width: 11px; height: 11px; flex: none; }
  /* Logo side */
  .card-back { left: 620px; top: 300px; background: var(--card-black); }
  .site-line {
    position: absolute; left: 34px; top: 30px;
    font-size: 12px; letter-spacing: 6px; color: var(--on-dark);
  }
  .card-back .logo-badge { width: 150px; height: 150px; left: 280px; top: 86px; font-size: 19px; }
</style>
</head>
<body>
  <section class="card card-front" aria-label="Contact side">
    <div class="edge-band">
      <span class="band-black"></span>
      <span class="band-beige"></span>
      <span class="band-teal"></span>
      <span class="band-pink"></span>
      <span class="band-black"></span>
    </div>
    <div class="logo-badge">Velvet<br>Lantern</div>
    <h1 class="holder-name">MIRA PELLOW</h1>
    <ul class="contact-list">
      <li>
        <svg viewBox="0 0 12 12" aria-hidden="true"><path d="M2.5 1 L4.5 1 L5.2 3.6 L3.9 4.6 Q5 7 7.4 8.1 L8.4 6.8 L11 7.5 L11 9.5 Q10 11 8.5 11 Q2.5 10 1 3.5 Q1 2 2.5 1 Z" fill="#1a1a1a"/></svg>
        555-013-4762
      </li>
      <li>
        <svg viewBox="0 0 12 12" aria-hidden="true"><circle cx="6" cy="6" r="5.5" fill="#1a1a1a"/><path d="M0.5 6 H11.5 M6 0.5 Q3 6 6 11.5 M6 0.5 Q9 6 6 11.5" stroke="#fff" stroke-width="0.8" fill="none"/></svg>
        www.velvetlantern.com
      </li>
      <li>
        <svg viewBox="0 0 12 12" aria-hidden="true"><rect x="0.5" y="0.5" width="11" height="11" rx="2" fill="#1a1a1a"/></svg>
        fb.me/VelvetLanternbyMira
      </li>
    </ul>
  </section>

  <section class="card card-back" aria-label="Logo side">
    <p class="site-line">www.velvetlantern.com</p>
    <div class="logo-badge">Velvet<br>Lantern</div>
  </section>
</body>
</html>
```